International business needs business cards

Our company, DRV Ventures Inc. is in the business of supplying a range construction products with particular emphasis on CEMENT. We have developed our own brand - TORVAN SUPPLIES - with which to infiltrate the market. We are launching our brand of cement (TORVAN Type IS Cement) into the Caribbean which is unlike anything this market has ever seen. A monopoly has existed here for the past 60-odd years and the market has now opened to allow the importation of other brands and consumers are anxious and ready for change/improvement. We are very excited to be launching and want to make a great first impression. We will be conducting workshops and seminars (from government level to the hardware store owners) and we want our business card to give us the strong, confident introduction that we need.

Target Market(s)

construction; builders; engineers; home owners

Industry/Entity Type

Construction

Contact Information for Business Card

Marisol Depree
CEO
cell # 1 555 4180736
Ground floor,Lindell Plaza Suite 2734
George Town,Grand Cayman
Cayman Islands,KY1-4823
EMAIL: m.depree@drvventuresinc.example
web site drvventuresinc.example

COMPANY: skype info drv.ventures.example

second card
Yvette Brannock-Depree
CFO
CELL# 1 555 607 3941
George Town,Grand Cayman
Cayman Islands,KY1-4823
EMAIL: y.brannockdepree@drvventuresinc.example
website drvventuresinc.example

Requirements
Must have
• Business cards must display BOTH logos - DRV is the company and TORVAN is the brand.

```html
<!DOCTYPE html>
<html lang="en">
<head>
<meta charset="utf-8">
<title>DRV Ventures Inc. — Business Cards</title>
<link href="https://fonts.googleapis.com/css2?family=Source+Sans+3:wght@400;600;700&display=swap" rel="stylesheet">
<style>
  :root {
    --backdrop: #3b3532;
    --card: #0d0c0c;
    --card-edge: #1c1a19;
    --accent-red: #8e1d1f;
    --copper: #b0714a;
    --text-light: #e6e3e0;
    --text-muted: #bdb8b3;
    --silver: #cfcfcf;
    --divider: #2a2827;
  }
  * { margin: 0; padding: 0; box-sizing: border-box; }
  html, body { width: 1200px; height: 900px; overflow: hidden; }
  body {
    background: var(--backdrop);
    font-family: "Source Sans 3", sans-serif;
    position: relative;
  }
  .card {
    position: absolute;
    top: 295px;
    width: 540px;
    height: 310px;
    background: var(--card);
    border: 1px solid var(--card-edge);
  }
  .card--contact { left: 45px; }
  .card--brand { left: 615px; }

  /* contact side */
  .company-mark {
    position: absolute;
    left: 36px;
    top: 186px;
    display: flex;
    align-items: center;
    gap: 12px;
  }
  .company-mark__square {
    width: 54px; height: 54px;
    background: var(--accent-red);
  }
  .company-mark__name {
    color: var(--text-light);
    font-weight: 700;
    font-size: 21px;
    line-height: 1.05;
    width: 110px;
  }
  .card__divider {
    position: absolute;
    left: 270px;
    top: 40px;
    width: 1px;
    height: 230px;
    background: var(--divider);
  }
  .contact {
    position: absolute;
    left: 296px;
    top: 44px;
    color: var(--text-light);
    font-size: 13.5px;
    line-height: 1.4;
  }
  .contact__name {
    color: var(--copper);
    font-weight: 600;
    font-size: 17px;
  }
  .contact__title { margin-bottom: 16px; }
  .contact__address { margin-bottom: 16px; }
  .contact__line {
    display: flex;
    align-items: center;
    gap: 9px;
  }
  .contact__icon { width: 10px; height: 10px; flex: none; }

  /* brand side */
  .brand-mark {
    position: absolute;
    left: 180px;
    top: 118px;
    display: flex;
    align-items: center;
    gap: 12px;
  }
  .brand-mark__square {
    width: 58px; height: 58px;
    background: var(--silver);
  }
  .brand-mark__name {
    color: var(--silver);
    font-weight: 700;
    font-size: 22px;
    line-height: 1.05;
    width: 120px;
  }
  .product-mark {
    position: absolute;
    right: 26px;
    top: 58px;
    display: flex;
    flex-direction: column;
    align-items: center;
    gap: 6px;
  }
  .product-mark__circle {
    width: 40px; height: 40px;
    border-radius: 50%;
    background: var(--silver);
  }
  .product-mark__name {
    color: var(--silver);
    font-weight: 600;
    font-size: 9px;
    letter-spacing: 0.08em;
  }
</style>
</head>
<body>
  <section class="card card--contact">
    <div class="company-mark">
      <div class="company-mark__square"></div>
      <div class="company-mark__name">DRV Ventures Inc.</div>
    </div>
    <div class="card__divider"></div>
    <div class="contact">
      <div class="contact__name">Marisol Depree</div>
      <div class="contact__title">CEO</div>
      <div class="contact__address">
        Ground floor, Lindell Plaza Suite<br>
        2734 George Town, Grand Cayman<br>
        Cayman Islands, KY1-4823
      </div>
      <div class="contact__line">
        <svg class="contact__icon" viewBox="0 0 10 10"><rect x="2.5" y="0.5" width="5" height="9" rx="1" fill="none" stroke="#b0714a"/></svg>
        <span>1 555 4180736</span>
      </div>
      <div class="contact__line">
        <svg class="contact__icon" viewBox="0 0 10 10"><rect x="0.5" y="2" width="9" height="6.5" fill="none" stroke="#b0714a"/><path d="M0.5 2 L5 6 L9.5 2" fill="none" stroke="#b0714a"/></svg>
        <span>m.depree@drvventuresinc.example</span>
      </div>
      <div class="contact__line">
        <svg class="contact__icon" viewBox="0 0 10 10"><circle cx="5" cy="5" r="4.5" fill="#b0714a"/><path d="M0.5 5 H9.5 M5 0.5 V9.5" stroke="#0d0c0c" stroke-width="0.8"/></svg>
        <span>www.drvventuresinc.example</span>
      </div>
    </div>
  </section>

  <section class="card card--brand">
    <div class="brand-mark">
      <div class="brand-mark__square"></div>
      <div class="brand-mark__name">DRV Ventures Inc.</div>
    </div>
    <div class="product-mark">
      <div class="product-mark__circle"></div>
      <div class="product-mark__name">TORVAN SUPPLIES</div>
    </div>
  </section>
</body>
</html>
```